Granite Tile Retail Website

We need wireframe PSD for a website selling granite tile. There are 4 custom pages, shopping cart page, and checkout page. I have a logo designed but the color scheme is up to you.
Color Gallery - We have approximately 20 different stone colors. Each color will have a little gallery of its own pictures. On this page the customer can also add a sample piece of the color they are viewing to their shopping cart.
Questions Page - This page has 3 elements
1. Upload or fax diagram of kitchen for quotation
2. Installation video
3. Installation FAQ (text)
Order Page - This page has 3 steps for the customer
1. Customer chooses his color.
2. For each color we have numerous different products. He inputs the quantity of each product.
3. Customer is given total price and shipping quote. If order over $500 it says "This order qualifies for free shipping". Customer can click on button to "Order Now"
Shopping Cart - Very standard, just like I have attached here. Just modify for your colors / font.
Checkout - Just like in the attached. See design-explanation.docx for minor adjustments.
I have vector file for logo.
Updates
Please try to post your designs by tonightÂ
Target Market(s)
Home owners 40-60 years old
Industry/Entity Type
Shopping
Look and feel

```html
<!DOCTYPE html>
<html lang="en">
<head>
<meta charset="utf-8">
<title>Stonecrest Granite – Colors Gallery</title>
<link rel="stylesheet" href="https://fonts.googleapis.com/css2?family=Oswald:wght@400;500;700&family=Open+Sans:wght@400&display=swap">
<style>
:root{
  --page-bg:#efefef;
  --card:#ffffff;
  --ink:#333333;
  --ink-dark:#222222;
  --maroon:#5a1a2e;
  --gold:#e8a93a;
  --gold-light:#f5c15a;
  --rule:#cfcfcf;
  --overlay:rgba(40,30,22,.78);
  --badge-gold:#d9b23a;
  --badge-blue:#1f5a92;
}
*{box-sizing:border-box;margin:0;padding:0}
html,body{width:864px;height:1200px;overflow:hidden}
body{background:var(--page-bg);font-family:"Oswald",sans-serif;color:var(--ink);position:relative}
.site{position:absolute;left:32px;top:26px;width:800px;height:1150px;background:var(--card);border:1px solid #e2e2e2}
.abs{position:absolute}

/* header */
.header{left:16px;top:20px;width:768px;height:96px;background:linear-gradient(#fafafa,#ededed);border-top:1px solid #e6e6e6;border-bottom:1px solid #dcdcdc}
.brand{left:24px;top:22px;display:flex;align-items:center;gap:8px}
.brand-mark{width:16px;height:16px;background:var(--gold)}
.brand-name{font-weight:700;color:var(--maroon);font-size:24px;line-height:26px;letter-spacing:1px}
.brand-name span{display:block;font-size:14px;letter-spacing:6px;line-height:16px}
.nav{right:24px;top:24px;display:flex;height:48px;align-items:center}
.nav a{font-size:16px;font-weight:500;color:var(--ink);text-decoration:none;padding:0 9px;line-height:48px;border-left:1px solid #b9b9b9}
.nav a:first-child{border-left:none}
.nav a.is-current{color:var(--gold)}

/* gallery */
.page-title{left:24px;top:152px;font-size:21px;line-height:24px;font-weight:500;color:var(--ink)}
.swatch{width:118px}
.swatch-label{font-size:13px;font-weight:500;line-height:14px;height:14px;color:var(--ink);white-space:nowrap}
.swatch-label small{font-size:10px;margin-right:3px}
.swatch-chip{width:118px;height:76px;border:2px solid rgba(0,0,0,.22)}
.divider{left:278px;top:198px;width:1px;height:830px;background:var(--rule)}

/* feature */
.feature-title{left:287px;top:193px;font-size:20px;line-height:20px;height:20px;font-weight:500;color:var(--ink);white-space:nowrap}
.feature-title small{font-size:13px;margin-right:4px}
.feature{left:288px;top:216px;width:496px;height:340px;border:3px solid var(--maroon);overflow:hidden}
.feature-photo{position:absolute;inset:0;background:linear-gradient(180deg,#b9c9c4 0%,#9fb1ac 35%,#a0663a 62%,#7a4a28 100%)}
.feature-panel{position:absolute;right:0;top:0;width:160px;height:100%;background:var(--overlay);padding:41px 10px 0 13px;color:#fff}
.feature-panel h3{font-size:16px;font-weight:500;line-height:23px;white-space:nowrap}
.feature-panel p{font-family:"Open Sans",sans-serif;font-size:11px;line-height:13.5px;margin-top:16px;text-indent:28px}
.sample-btn{position:absolute;left:13px;top:301px;width:133px;height:27px;background:linear-gradient(var(--gold-light),var(--gold));display:flex;align-items:center;padding-left:10px;gap:8px;font-size:12px;font-weight:500;color:var(--ink-dark);text-decoration:none}

.thumb{width:119px;height:78px;border:1px solid #6a3b1f}
.thumb-a{background:linear-gradient(135deg,#8d8f8a,#5d5a52 60%,#3b3530)}
.thumb-b{background:linear-gradient(135deg,#8a2a12,#5b1c10 55%,#1d1515)}
.thumb-c{background:linear-gradient(135deg,#c98a3a,#7a3a18 55%,#2a1810)}

/* footer */
.footer{left:16px;top:1050px;width:768px;height:98px;background:linear-gradient(#f4f4f4,#ffffff);border-top:1px solid #e0e0e0}
.footer-col{top:18px;display:flex;flex-direction:column}
.footer-col a{font-size:11.5px;line-height:15.3px;color:var(--ink-dark);text-decoration:none;font-weight:400}
.footer-col a.is-current{color:var(--gold)}
.badge-round{left:586px;top:16px;width:56px;height:56px;border-radius:50%;background:radial-gradient(#f3d56a,var(--badge-gold))}
.badge-box{left:651px;top:16px;width:93px;height:34px;border-radius:4px;background:var(--badge-blue)}
.pay-note{left:652px;top:56px;font-family:"Open Sans",sans-serif;font-size:10px;line-height:12px;color:#2a5a9a}
.pay-box{left:661px;top:70px;width:80px;height:18px;border-radius:3px;background:#2a5a9a}
</style>
</head>
<body>
<div class="site">
  <header class="header abs">
    <div class="brand abs">
      <div class="brand-mark"></div>
      <div class="brand-name">STONECREST<span>GRANITE</span></div>
    </div>
    <nav class="nav abs">
      <a href="#">HOME</a>
      <a href="#" class="is-current">GALLERY</a>
      <a href="#">QUESTIONS</a>
      <a href="#">ORDER</a>
      <a href="#">SHOPPING CART</a>
    </nav>
  </header>

  <h1 class="page-title abs">COLORS GALLERY</h1>

  <div class="swatch abs" style="left:17px;top:184px"><div class="swatch-label"><small>01.</small>GIALLO</div><div class="swatch-chip" style="background:#a87a5a"></div></div>
  <div class="swatch abs" style="left:154px;top:184px"><div class="swatch-label"><small>02.</small>TAR BROWN</div><div class="swatch-chip" style="background:#dcb99a"></div></div>
  <div class="swatch abs" style="left:17px;top:278px"><div class="swatch-label"><small>03.</small>MERT BROWN</div><div class="swatch-chip" style="background:#f1e0cc"></div></div>
  <div class="swatch abs" style="left:154px;top:278px"><div class="swatch-label"><small>04.</small>VBA TUBA</div><div class="swatch-chip" style="background:#4d2a17"></div></div>
  <div class="swatch abs" style="left:17px;top:373px"><div class="swatch-label"><small>05.</small>GIALLO</div><div class="swatch-chip" style="background:#35352a"></div></div>
  <div class="swatch abs" style="left:154px;top:373px"><div class="swatch-label"><small>06.</small>TAR BROWN</div><div class="swatch-chip" style="background:#4a1631"></div></div>
  <div class="swatch abs" style="left:17px;top:467px"><div class="swatch-label"><small>07.</small>MERT BROWN</div><div class="swatch-chip" style="background:#282b33"></div></div>
  <div class="swatch abs" style="left:154px;top:467px"><div class="swatch-label"><small>08.</small>VBA TUBA</div><div class="swatch-chip" style="background:#7d8190"></div></div>
  <div class="swatch abs" style="left:17px;top:562px"><div class="swatch-label"><small>09.</small>GIALLO</div><div class="swatch-chip" style="background:#7d6759"></div></div>
  <div class="swatch abs" style="left:154px;top:562px"><div class="swatch-label"><small>10.</small>TAR BROWN</div><div class="swatch-chip" style="background:#879652"></div></div>
  <div class="swatch abs" style="left:17px;top:656px"><div class="swatch-label"><small>11.</small>MERT BROWN</div><div class="swatch-chip" style="background:#a2817a"></div></div>
  <div class="swatch abs" style="left:154px;top:656px"><div class="swatch-label"><small>12.</small>VBA TUBA</div><div class="swatch-chip" style="background:#4a524a"></div></div>
  <div class="swatch abs" style="left:17px;top:751px"><div class="swatch-label"><small>13.</small>GIALLO</div><div class="swatch-chip" style="background:#2c2c2e"></div></div>
  <div class="swatch abs" style="left:154px;top:751px"><div class="swatch-label"><small>14.</small>TAR BROWN</div><div class="swatch-chip" style="background:#4a4240"></div></div>
  <div class="swatch abs" style="left:17px;top:845px"><div class="swatch-label"><small>15.</small>MERT BROWN</div><div class="swatch-chip" style="background:#4a5a52"></div></div>
  <div class="swatch abs" style="left:154px;top:845px"><div class="swatch-label"><small>16.</small>VBA TUBA</div><div class="swatch-chip" style="background:#363738"></div></div>
  <div class="swatch abs" style="left:17px;top:940px"><div class="swatch-label"><small>17.</small>VBA TUBA</div><div class="swatch-chip" style="background:#7a1030"></div></div>

  <div class="divider abs"></div>

  <h2 class="feature-title abs"><small>06.</small>TAR BROWN</h2>
  <section class="feature abs">
    <div class="feature-photo" role="img" aria-label="Kitchen with wooden cabinets and dark granite countertop"></div>
    <div class="feature-panel">
      <h3>SOME TEXT<br>GOES HERE - THE<br>MAIN IDEA OF THE<br>CHOSEN GRANITE</h3>
      <p>Donec quam felis, ultricies nec, pellen tesque eu, pretium quis, sem. Nulla consequat massa quis enim, frin-gilla vel, aliquet nlojec, vulputate eget, argtcu. Vitae, justo.</p>
      <a class="sample-btn" href="#">
        <svg width="16" height="14" viewBox="0 0 16 14" aria-hidden="true"><path d="M0 1h3l2 8h8l2-6H4" fill="none" stroke="#222" stroke-width="1.6"/><circle cx="6" cy="12" r="1.3" fill="#222"/><circle cx="12" cy="12" r="1.3" fill="#222"/></svg>
        ORDER A SAMPLE »
      </a>
    </div>
  </section>

  <div class="thumb thumb-a abs" style="left:288px;top:574px" role="img" aria-label="Kitchen countertop detail"></div>
  <div class="thumb thumb-b abs" style="left:413px;top:574px" role="img" aria-label="Kitchen with cherry cabinets"></div>
  <div class="thumb thumb-c abs" style="left:538px;top:574px" role="img" aria-label="Warm lit kitchen interior"></div>
  <div class="thumb thumb-b abs" style="left:664px;top:574px" role="img" aria-label="Kitchen with cherry cabinets"></div>
  <div class="thumb thumb-b abs" style="left:288px;top:658px" role="img" aria-label="Kitchen with cherry cabinets"></div>
  <div class="thumb thumb-c abs" style="left:413px;top:658px" role="img" aria-label="Warm lit kitchen interior"></div>
  <div class="thumb thumb-a abs" style="left:538px;top:658px" role="img" aria-label="Kitchen countertop detail"></div>
  <div class="thumb thumb-c abs" style="left:664px;top:658px" role="img" aria-label="Warm lit kitchen interior"></div>
  <div class="thumb thumb-a abs" style="left:288px;top:741px" role="img" aria-label="Kitchen countertop detail"></div>
  <div class="thumb thumb-b abs" style="left:413px;top:741px" role="img" aria-label="Kitchen with cherry cabinets"></div>
  <div class="thumb thumb-c abs" style="left:538px;top:741px" role="img" aria-label="Warm lit kitchen interior"></div>

  <footer class="footer abs">
    <div class="footer-col abs" style="left:25px">
      <a href="#">HOME</a><a href="#" class="is-current">GALLERY</a><a href="#">QUESTIONS</a><a href="#">ORDER</a><a href="#">SHOPPING CART</a>
    </div>
    <div class="footer-col abs" style="left:195px">
      <a href="#">RETURN POLICY</a><a href="#">SHIPPING POLICY</a><a href="#">PRIVACY</a><a href="#">TERMS OF USE</a><a href="#">CUSTOMER SERVICE</a>
    </div>
    <div class="footer-col abs" style="left:384px">
      <a href="#">NEW LINK</a><a href="#">ANOTHER LINK</a><a href="#">THIRD LINK</a><a href="#">FOURTH LINK</a><a href="#">FIFTH LINK</a>
    </div>
    <div class="badge-round abs" aria-hidden="true"></div>
    <div class="badge-box abs" aria-hidden="true"></div>
    <div class="pay-note abs">Pay Securely With</div>
    <div class="pay-box abs" aria-hidden="true"></div>
  </footer>
</div>
</body>
</html>
```